Brindle Sky Port needs a new upscale business card design for our high end aircraft hangar complex

Brindle Sky Port (BSP) is a large, upscale jet hangar complex in the US housing expensive aircraft. We need a new business card design, using our current logo. We will be attending a industry convention and need a card design that will stand out and be remembered by aircraft owners and private pilots.

Target Market(s)

Aircraft pilots or owners looking for a new upscale hangar

Industry/Entity Type

Airport

Contact Information for Business Card

I like to use very heavy card stock, 400#, double sided. Square, no rounded edges please.

Colors
3276b5
0255a3
85abd2

Requirements
Must have
• An expensive, classy design, vivid colors.
Nice to have
• Needs to look very expensive and classy, and have some "pop". Designer must be able to download or copy my current typeface or fonts.
• One card side might be black with the "Logo and Brindle Sky Port Double line image in blue (or try gold, or glossy black), and perhaps have a grayed out "K720 jet silhouette". The other card side would have our contact info, and perhaps the "BSP Logo only". I'd like my contact info 'stacked', not in a paragraph format.
Should not have
• Should not look "too busy". Having a double-sided card will help.

```html
<!DOCTYPE html>
<html lang="en">
<head>
<meta charset="utf-8">
<title>Brindle Sky Port – Business Card</title>
<link rel="stylesheet" href="https://fonts.googleapis.com/css2?family=Open+Sans:wght@400;600;700&display=swap">
<style>
  :root {
    --backdrop: #3a3a3a;
    --card: #111214;
    --card-edge: #1c1d20;
    --brand-blue: #3276b5;
    --brand-deep: #0255a3;
    --brand-light: #85abd2;
    --text-light: #e6e8eb;
    --text-muted: #b9bdc3;
    --divider: #2c2e32;
  }
  * { box-sizing: border-box; margin: 0; padding: 0; }
  html, body {
    width: 1200px;
    height: 900px;
    overflow: hidden;
    background: var(--backdrop);
    font-family: "Open Sans", Arial, sans-serif;
  }
  .canvas {
    position: relative;
    width: 1200px;
    height: 900px;
    display: flex;
    align-items: center;
    justify-content: center;
    gap: 40px;
  }
  .card {
    position: relative;
    width: 500px;
    height: 286px;
    background: var(--card);
    border: 1px solid var(--card-edge);
    border-radius: 0;
    box-shadow: 0 18px 40px rgba(0,0,0,.45);
  }

  /* Contact side */
  .card--contact { display: flex; }
  .contact-mark {
    width: 250px;
    display: flex;
    align-items: center;
    justify-content: center;
    padding-top: 30px;
  }
  .monogram {
    font-weight: 700;
    font-size: 64px;
    line-height: 1;
    letter-spacing: 4px;
    color: var(--brand-blue);
  }
  .contact-divider {
    width: 1px;
    margin: 36px 0;
    background: var(--divider);
  }
  .contact-details {
    padding: 44px 16px 0 24px;
    color: var(--text-light);
    font-size: 13px;
    line-height: 17px;
    white-space: nowrap;
  }
  .person-name {
    color: var(--brand-blue);
    font-weight: 600;
    font-size: 15px;
    line-height: 18px;
  }
  .person-role { margin-bottom: 18px; }
  .address { margin-bottom: 16px; }
  .contact-list { list-style: none; }
  .contact-list li {
    display: flex;
    align-items: center;
    gap: 8px;
  }
  .contact-list svg {
    width: 10px;
    height: 10px;
    fill: var(--brand-blue);
    flex: none;
  }

  /* Brand side */
  .card--brand {
    display: flex;
    flex-direction: column;
    align-items: center;
    justify-content: center;
    gap: 4px;
  }
  .brand-monogram {
    font-weight: 700;
    font-size: 72px;
    line-height: 1;
    letter-spacing: 4px;
    color: var(--brand-deep);
  }
  .brand-name {
    font-weight: 700;
    font-size: 24px;
    line-height: 1.2;
    color: var(--brand-deep);
  }
</style>
</head>
<body>
<main class="canvas">
  <section class="card card--contact" aria-label="Contact side">
    <div class="contact-mark">
      <span class="monogram">BSP</span>
    </div>
    <div class="contact-divider"></div>
    <div class="contact-details">
      <p class="person-name">Calder Wynn</p>
      <p class="person-role">Managing Director</p>
      <p class="address">4810 Hangar Row Drive<br>Country Name, 123456.</p>
      <ul class="contact-list">
        <li>
          <svg viewBox="0 0 10 10" aria-hidden="true"><path d="M2 0.5 L3.6 2.6 L2.7 3.6 Q4 6 6.4 7.3 L7.4 6.4 L9.5 8 L8.4 9.5 Q3.5 9 0.5 1.6 Z"/></svg>
          <span>044-555 210 347</span>
        </li>
        <li>
          <svg viewBox="0 0 10 10" aria-hidden="true"><path d="M0.5 2 H9.5 V8 H0.5 Z M1.2 2.6 L5 5.4 L8.8 2.6 Z" fill-rule="evenodd"/></svg>
          <span>044-555 210 347</span>
        </li>
        <li>
          <svg viewBox="0 0 10 10" aria-hidden="true"><path d="M0.5 1.5 H9.5 V8.5 H0.5 Z M1.5 3.5 V7.5 H8.5 V3.5 Z" fill-rule="evenodd"/></svg>
          <span>info@brindlesky.com</span>
        </li>
        <li>
          <svg viewBox="0 0 10 10" aria-hidden="true"><path d="M1 6 L4 3 L5 4 L2 7 Z M5 6 L8 3 L9 4 L6 7 Z M3.5 5.5 L6 3 L7 4 L4.5 6.5 Z"/></svg>
          <span>www.brindleskyport.com</span>
        </li>
      </ul>
    </div>
  </section>

  <section class="card card--brand" aria-label="Brand side">
    <span class="brand-monogram">BSP</span>
    <span class="brand-name">Brindle Sky Port</span>
  </section>
</main>
</body>
</html>
```